Valdane Companies Business Card Design

We need a new business card for our Private Equity Real Estate Development firm, “Valdane” and our EB-5 regional center “Thornmere Regional Center” on one card. We prefer a design that is simple, elegant, and represents the luxury products we design and build as well as the financial security and stability our successful history has produced. We are an industry leader in our field and 3rd generation family business that has evolved into an institutional quality investment platform. Considered design size is standard business card dimensions (3.5 x 2 inches with an additional 1/8 inch space for design elements or backgrounds that extend beyond the finished size of your piece.

Target Market(s)

• High net worth individuals
• Highly skilled technical workers and physicians in the US seeking investment-based immigration opportunities
• Sophisticated private equity investors
• Intermediary partners include domestic attorneys and investment brokers, as well as international agent networks
• US real estate developers

Industry/Entity Type

Finance

Contact Information for Business Card

(Providing placeholder info for personal information, please design for longer character spaces, longer names and addresses etc..)
• Logo for Valdane
• Logo for Thornmere Regional Center
• Full name: Marcus Valdane
• Job title: CEO
• Email address: mvaldane@valdanecompanies.com
• Cell phone number: +1.555.314.2287
• Office number +1.555.628.4410
• Office address: Larkfield Court 5, 4817 Vista Orilla, Corvell Springs, CV.
• Website: www.valdanecompanies.com

Font styles to use
Serif
Sans Serif

Colors
ec1f27
ffffff
000000

Requirements
Must have
• • Logo for Valdane
• • Logo for Thornmere Regional Center
• - Use rounded corners
• (See .ai file included for logos)
Nice to have
• • Simple, elegant design
• • Aesthetically compatible with our website design (www.valdanecompanies.com)
• • Color palette including but not limited to white, black, and red (as per logos)
Should not have
• - Not too much red color
• - Do not stack both logos on top of each other

```html
<!DOCTYPE html>
<html lang="en">
<head>
<meta charset="utf-8">
<title>Valdane Companies Business Card</title>
<link rel="stylesheet" href="https://fonts.googleapis.com/css2?family=EB+Garamond:wght@500;600;700&display=swap">
<style>
  :root {
    --backdrop: #3a3a3c;
    --card-black: #0d0d0d;
    --card-white: #ececec;
    --ink: #161616;
    --ink-soft: #2a2a2a;
    --mark-grey: #4a4a4a;
    --brand-red: #9e1a2c;
    --line-grey: #8a8a8a;
  }
  html, body {
    margin: 0;
    padding: 0;
    width: 1200px;
    height: 1000px;
    overflow: hidden;
    background: var(--backdrop);
  }
  .canvas {
    position: relative;
    width: 1200px;
    height: 1000px;
    font-family: "EB Garamond", Georgia, serif;
  }
  .card {
    position: absolute;
    left: 250px;
    width: 700px;
    height: 400px;
    border-radius: 28px;
    box-sizing: border-box;
  }

  /* Back side */
  .card-back {
    top: 70px;
    background: var(--card-black);
    display: flex;
    align-items: center;
    justify-content: center;
    gap: 18px;
  }
  .card-back .brand-square {
    width: 34px;
    height: 34px;
    background: var(--mark-grey);
  }
  .card-back .brand-name {
    font-weight: 600;
    font-size: 54px;
    letter-spacing: 3px;
    text-transform: uppercase;
    color: var(--mark-grey);
  }

  /* Front side */
  .card-front {
    top: 530px;
    background: var(--card-white);
    color: var(--ink);
  }
  .front-brand {
    position: absolute;
    left: 42px;
    top: 34px;
    display: flex;
    align-items: center;
    gap: 14px;
  }
  .front-brand .brand-square {
    width: 30px;
    height: 30px;
    background: var(--ink-soft);
  }
  .front-brand .divider {
    width: 1px;
    height: 38px;
    background: var(--line-grey);
  }
  .front-brand .brand-name {
    font-weight: 600;
    font-size: 46px;
    letter-spacing: 2px;
    text-transform: uppercase;
    color: var(--ink-soft);
  }
  .regional-center {
    position: absolute;
    right: 40px;
    top: 160px;
    display: flex;
    align-items: center;
    gap: 10px;
  }
  .regional-center .center-square {
    width: 22px;
    height: 22px;
    background: var(--brand-red);
  }
  .regional-center .center-name {
    font-weight: 600;
    font-size: 22px;
    color: var(--brand-red);
  }
  .contact {
    position: absolute;
    left: 42px;
    top: 228px;
    font-weight: 600;
    font-size: 17px;
    line-height: 1.35;
  }
  .contact .person {
    margin: 0 0 6px;
    font-weight: 700;
    font-size: 22px;
    color: var(--brand-red);
    text-transform: uppercase;
  }
  .contact .person .role {
    font-size: 13px;
    color: var(--ink);
    margin-left: 8px;
  }
  .contact p { margin: 0; }
  .contact .label { color: var(--brand-red); }
  .contact .gap { display: inline-block; width: 14px; }
</style>
</head>
<body>
<div class="canvas">
  <section class="card card-back" aria-label="Card back">
    <span class="brand-square"></span>
    <span class="brand-name">Valdane Capital</span>
  </section>

  <section class="card card-front" aria-label="Card front">
    <div class="front-brand">
      <span class="brand-square"></span>
      <span class="divider"></span>
      <span class="brand-name">Valdane</span>
    </div>

    <div class="regional-center">
      <span class="center-square"></span>
      <span class="center-name">Thornmere Regional Center</span>
    </div>

    <div class="contact">
      <p class="person">Marcus Valdane<span class="role">CEO</span></p>
      <p><span class="label">cell:</span> +1.555.314.2287<span class="gap"></span><span class="label">office:</span> +1.555.628.4410</p>
      <p>mvaldane@valdanecompanies.com &nbsp;|&nbsp; www.valdanecompanies.com</p>
      <p>Larkfield Court 5, 4817 Vista Orilla, Corvell Springs, CV.</p>
    </div>
  </section>
</div>
</body>
</html>
```